Vortel surface design based website for technology jobs website

We need a website design for a technology job listing website, mainly aiming at 20/30/40 year old nerds. Jobs listed from multiple sources will be concatenated and organised. This website will be built with Vortel surface design (https://surfacekit.example/guidelines/) so please use their components. The design should be simple and clear, so a user can directly look for offerings that are interesting for him.

Three different pages will be needed:

1. Main jobs list page

Contains a large table (https://surfacekit.example/guidelines/components/data-tables.html#data-tables-structure), on top or next to this data-table users should be able to apply filters (select countries, select salary ranges) and somewhere an overview of the selected filters should be shown.

- A subscribe bar should be shown somewhere to allow a user to register for weekly/monthly mailings for new job offers with his preferred search filters.

2. Selected item page

If an item is clicked, a user should be able to view a job posting and it's details.

3. An advertiser should be able post his job offer.
Similar fields as https://post.ledgerworkboard.example/.
(https://surfacekit.example/guidelines/components/text-fields.html#text-fields-layout)

Target Market(s)

20/30/40 year old nerds.

Industry/Entity Type

Computer

Logo Text

TechHirePlaza.example

Number of Pages Required

3 page

Colors

Designer to choose colors to be used in the design.

Requirements
Must have
• 1. Main jobs list page
• Contains a large table (https://surfacekit.example/guidelines/components/data-tables.html#data-tables-structure), on top or next to this data-table users should be able to apply filters (select countries, select salary ranges) and somewhere an overview of the selected filters should be shown.
• - A subscribe bar should be shown somewhere to allow a user to register for weekly/monthly mailings for new job offers with his preferred search filters.
• 2. Selected item page
• If an item is clicked, a user should be able to view a job posting and it's details.
• 3. An advertiser should be able post his job offer,
• (https://surfacekit.example/guidelines/components/text-fields.html#text-fields-layout)
• Please use open fonts!

```html
<!DOCTYPE html>
<html lang="en">
<head>
<meta charset="utf-8">
<title>Jobs List</title>
<link href="https://fonts.googleapis.com/css2?family=Roboto:wght@400;500;700&family=Open+Sans:wght@400&display=swap" rel="stylesheet">
<style>
:root{
  --header-blue:#0158a0;
  --band-blue:#04a9f0;
  --button-blue:#0559a0;
  --page-bg:#efefef;
  --card:#ffffff;
  --row-alt:#f4f4f4;
  --line:#e3e3e3;
  --text:#333a40;
  --muted:#6a6f75;
  --fab:#d84132;
  --footer:#2b2f36;
  --drawer:rgba(34,36,40,0.95);
  --active:#0a9de0;
}
*{box-sizing:border-box;margin:0;padding:0}
html,body{width:1200px;height:1086px;overflow:hidden}
body{position:relative;background:var(--page-bg);font-family:Roboto,Arial,sans-serif;color:var(--text)}
.header{position:absolute;left:0;top:0;width:1200px;height:398px;background:var(--header-blue)}
.logo{position:absolute;top:6px;left:0;width:1200px;text-align:center;color:#fff;font-weight:700;font-size:32px}
.search-band{position:absolute;left:114px;top:105px;width:1000px;height:98px;background:var(--band-blue)}
.field{position:absolute;top:29px;height:41px;background:#fff;border-radius:2px;font-size:12.5px;color:#8a8f94;padding:12px 7px;white-space:nowrap;overflow:hidden}
.field svg{position:absolute;right:8px;top:17px}
.search-btn{position:absolute;left:870px;top:29px;width:101px;height:41px;background:var(--button-blue);border-radius:2px}
.search-btn svg{position:absolute;left:40px;top:10px}
.card{position:absolute;left:84px;top:267px;width:1032px;height:729px;background:var(--card);box-shadow:0 1px 3px rgba(0,0,0,.25)}
.table{position:absolute;left:0;top:0;width:1032px;font-size:12.5px}
.thead{position:absolute;top:50px;left:0;width:100%;height:30px;border-bottom:1px solid var(--line)}
.row{position:absolute;left:0;width:100%;height:50px;border-bottom:1px solid #ececec}
.row.alt{background:var(--row-alt)}
.cell{position:absolute;top:17px;white-space:nowrap;color:var(--muted)}
.thead .cell{top:0;color:var(--text)}
.c-box{left:21px;top:18px;width:13px;height:13px;border:1px solid #bbb;border-radius:2px}
.c-type{left:35px;color:#1e6fb0}
.c-country{left:243px;color:var(--text)}
.c-exp{left:428px;color:var(--text)}
.c-sal{left:591px}
.c-skill{left:728px}
.c-emp{left:878px}
.fab{position:absolute;left:1128px;top:936px;width:60px;height:60px;border-radius:50%;background:var(--fab);box-shadow:0 2px 5px rgba(0,0,0,.3)}
.fab svg{position:absolute;left:19px;top:19px}
.footer{position:absolute;left:0;top:1045px;width:1200px;height:41px;background:var(--footer);color:#fff;font-family:"Open Sans",Arial,sans-serif;font-size:12px;text-align:center;line-height:41px}
.drawer{position:absolute;left:0;top:0;width:228px;height:1086px;background:var(--drawer)}
.drawer .close{position:absolute;left:186px;top:9px}
.menu{list-style:none;position:absolute;left:11px;top:54px;width:205px}
.menu li{height:38.7px;padding-left:41px;padding-top:7px;color:#fff;font-weight:700;font-size:12.5px;word-spacing:3px}
.menu li.active{background:#fff;color:var(--active);height:27px}
.menu li.active+li{margin-top:11.7px}
</style>
</head>
<body>
<header class="header">
  <div class="logo">Logo Name</div>
  <div class="search-band">
    <div class="field" style="left:2px;width:292px">Keyword (Job Title, Description,Tags)<svg width="9" height="6"><path d="M1 1l3.5 3.5L8 1" fill="none" stroke="#888"/></svg></div>
    <div class="field" style="left:302px;width:215px">Select Location<svg width="9" height="6"><path d="M1 1l3.5 3.5L8 1" fill="none" stroke="#888"/></svg></div>
    <div class="field" style="left:526px;width:213px">Salary<svg width="9" height="6"><path d="M1 1l3.5 3.5L8 1" fill="none" stroke="#888"/></svg></div>
    <div class="field" style="left:748px;width:113px">Designation<svg width="9" height="6"><path d="M1 1l3.5 3.5L8 1" fill="none" stroke="#888"/></svg></div>
    <div class="search-btn"><svg width="21" height="21" viewBox="0 0 21 21"><circle cx="8.5" cy="8.5" r="6.5" fill="none" stroke="#fff" stroke-width="3"/><path d="M13.5 13.5l5.5 5.5" stroke="#fff" stroke-width="3.4" stroke-linecap="round"/></svg></div>
  </div>
</header>

<main class="card">
  <div class="table">
    <div class="thead">
      <span class="cell c-type" style="color:#999">Job Type</span>
      <span class="cell c-country">Country Name</span>
      <span class="cell c-exp">Experience</span>
      <span class="cell c-sal" style="color:var(--text)">Salary</span>
      <span class="cell c-skill" style="color:var(--text)">Keyskills</span>
      <span class="cell c-emp" style="color:var(--text)">Employment Type</span>
    </div>
    <div class="row" style="top:81px"><span class="cell c-box"></span><span class="cell c-type">Software Engineer</span><span class="cell c-country">Country</span><span class="cell c-exp">0 -1</span><span class="cell c-sal">$ 20000</span><span class="cell c-skill">HTML Javascript ⌄</span><span class="cell c-emp">Full Time</span></div>
    <div class="row alt" style="top:131px"><span class="cell c-box"></span><span class="cell c-type">Software Engineer</span><span class="cell c-country">Country</span><span class="cell c-exp">0 -1</span><span class="cell c-sal">$ 20000</span><span class="cell c-skill">HTML Javascript ⌄</span><span class="cell c-emp">Full Time</span></div>
    <div class="row" style="top:181px"><span class="cell c-box"></span><span class="cell c-type">Software Engineer</span><span class="cell c-country">Country</span><span class="cell c-exp">0 -1</span><span class="cell c-sal">$ 20000</span><span class="cell c-skill">HTML Javascript ⌄</span><span class="cell c-emp">Full Time</span></div>
    <div class="row" style="top:231px"><span class="cell c-box"></span><span class="cell c-type">Software Engineer</span><span class="cell c-country">Country</span><span class="cell c-exp">0 -1</span><span class="cell c-sal">$ 20000</span><span class="cell c-skill">HTML Javascript ⌄</span><span class="cell c-emp">Full Time</span></div>
    <div class="row" style="top:281px"><span class="cell c-box"></span><span class="cell c-type">Software Engineer</span><span class="cell c-country">Country</span><span class="cell c-exp">0 -1</span><span class="cell c-sal">$ 20000</span><span class="cell c-skill">HTML Javascript ⌄</span><span class="cell c-emp">Full Time</span></div>
    <div class="row" style="top:331px"><span class="cell c-box"></span><span class="cell c-type">Software Engineer</span><span class="cell c-country">Country</span><span class="cell c-exp">0 -1</span><span class="cell c-sal">$ 20000</span><span class="cell c-skill">HTML Javascript ⌄</span><span class="cell c-emp">Full Time</span></div>
    <div class="row" style="top:381px"><span class="cell c-box"></span><span class="cell c-type">Software Engineer</span><span class="cell c-country">Country</span><span class="cell c-exp">0 -1</span><span class="cell c-sal">$ 20000</span><span class="cell c-skill">HTML Javascript ⌄</span><span class="cell c-emp">Full Time</span></div>
    <div class="row" style="top:431px"><span class="cell c-box"></span><span class="cell c-type">Software Engineer</span><span class="cell c-country">Country</span><span class="cell c-exp">0 -1</span><span class="cell c-sal">$ 20000</span><span class="cell c-skill">HTML Javascript ⌄</span><span class="cell c-emp">Full Time</span></div>
    <div class="row" style="top:481px"><span class="cell c-box"></span><span class="cell c-type">Software Engineer</span><span class="cell c-country">Country</span><span class="cell c-exp">0 -1</span><span class="cell c-sal">$ 20000</span><span class="cell c-skill">HTML Javascript ⌄</span><span class="cell c-emp">Full Time</span></div>
    <div class="row" style="top:531px"><span class="cell c-box"></span><span class="cell c-type">Software Engineer</span><span class="cell c-country">Country</span><span class="cell c-exp">0 -1</span><span class="cell c-sal">$ 20000</span><span class="cell c-skill">HTML Javascript ⌄</span><span class="cell c-emp">Full Time</span></div>
    <div class="row" style="top:581px"><span class="cell c-box"></span><span class="cell c-type">Software Engineer</span><span class="cell c-country">Country</span><span class="cell c-exp">0 -1</span><span class="cell c-sal">$ 20000</span><span class="cell c-skill">HTML Javascript ⌄</span><span class="cell c-emp">Full Time</span></div>
    <div class="row" style="top:631px"><span class="cell c-box"></span><span class="cell c-type">Software Engineer</span><span class="cell c-country">Country</span><span class="cell c-exp">0 -1</span><span class="cell c-sal">$ 20000</span><span class="cell c-skill">HTML Javascript ⌄</span><span class="cell c-emp">Full Time</span></div>
  </div>
</main>

<div class="fab"><svg width="22" height="22"><path d="M11 1v20M1 11h20" stroke="#fff" stroke-width="2"/></svg></div>

<footer class="footer">Copyright © website address I All Rights Reaserved</footer>

<nav class="drawer">
  <svg class="close" width="26" height="26" viewBox="0 0 26 26"><circle cx="13" cy="13" r="12" fill="none" stroke="#fff" stroke-width="1.5"/><path d="M8.5 8.5l9 9M17.5 8.5l-9 9" stroke="#fff" stroke-width="1.5"/></svg>
  <ul class="menu">
    <li class="active">Menu 01</li>
    <li>Menu 02</li>
    <li>Menu 03</li>
    <li>Menu 04</li>
    <li>Menu 05</li>
    <li>Menu 06</li>
    <li>Menu 07</li>
    <li>Menu 08</li>
    <li>Menu 09</li>
    <li>Menu 10</li>
  </ul>
</nav>
</body>
</html>
```